Website for Torvel Capital - investment banking firm

We have a corporate identity (thanks to Ravinka/31842) and want to extend that into a website design.  See the attached zipped files.
We have software folks in-house to do the coding.
See the attached Project Brief & Notes for more details.  Don't worry about the actual text - lorem ipsum will be fine.
The server will be Apache.
Thank you!
Desmond

Industry/Entity Type
Investment

```html
<!DOCTYPE html>
<html lang="en">
<head>
<meta charset="utf-8">
<title>Torvel Capital</title>
<link href="https://fonts.googleapis.com/css2?family=Open+Sans:wght@300;400;600&family=Raleway:wght@300;400;700&display=swap" rel="stylesheet">
<style>
:root{
  --navy:#0d3b78;
  --hero-a:#1b4d86;
  --hero-b:#2e66a3;
  --link-blue:#1a4f8f;
  --accent:#1f9be3;
  --ink:#333;
  --muted:#555;
  --caption:#0c1a2b;
  --maroon:#8a1d2c;
  --btn:#5c86b8;
}
*{margin:0;padding:0;box-sizing:border-box}
html,body{width:1200px;height:1051px;overflow:hidden;background:#fff}
body{position:relative;font-family:"Open Sans",sans-serif;color:var(--ink)}
.abs{position:absolute}

.top-bar{left:0;top:0;width:1200px;height:37px;background:linear-gradient(#1b4a84,#0f3566)}
.top-bar a{position:absolute;top:10px;color:#fff;font-size:12.5px;text-decoration:none}
.search{left:583px;top:6px;width:250px;height:25px;background:#41638e;color:#9fb4cf;font-size:12px;padding:6px 12px}
.search svg{position:absolute;right:10px;top:6px}
.flag{left:1006px;top:9px;width:25px;height:16px;border:1px solid #ddd}
.flag i{display:block;height:50%}

.header{left:0;top:37px;width:1200px;height:83px;border-bottom:3px solid #e3e3e3;background:#fff}
.brand{left:148px;top:22px;display:flex;align-items:center;gap:10px}
.brand-mark{width:40px;height:40px;background:var(--navy)}
.brand-name{font-size:27px;font-weight:400;color:var(--navy);letter-spacing:1px}
.nav a{position:absolute;top:35px;font-size:16px;color:#222;text-decoration:none}
.nav a.active{color:var(--link-blue)}

.hero{left:0;top:120px;width:1200px;height:533px;background:radial-gradient(ellipse at 70% 40%,var(--hero-b),var(--hero-a) 70%)}
.hero-title{position:absolute;left:146px;top:128px;font-family:"Raleway",sans-serif;font-weight:300;font-size:45px;line-height:56px;color:#fff}
.hero-title b{font-weight:700}
.hero-lead{position:absolute;left:148px;top:250px;width:480px;font-weight:300;font-size:20px;line-height:28px;color:#fff}
.btn{position:absolute;left:149px;top:325px;width:137px;height:32px;background:var(--btn);color:#fff;font-weight:700;font-size:16px;padding:5px 10px;font-family:"Raleway",sans-serif}
.globe{left:609px;top:92px;width:314px;height:402px;border-radius:50% 50% 20% 20%;background:radial-gradient(circle at 50% 38%,#9aa08a,#6b735e 45%,rgba(60,70,60,.2) 62%,transparent 70%)}
.caption{left:683px;top:246px;width:388px;height:100px;background:var(--caption);border-left:11px solid #fff;padding:14px 18px;color:#fff}
.caption-title{font-family:"Raleway",sans-serif;font-weight:400;font-size:20px;line-height:26px}
.caption-title span,.caption-text a{color:var(--accent)}
.caption-text{font-family:"Raleway",sans-serif;font-size:12px;line-height:19px;margin-top:6px}
.dots{left:962px;top:346px;width:109px;height:64px;background:var(--caption);padding:12px 24px;display:flex;gap:5px}
.dots i{width:9px;height:9px;border-radius:50%;background:#fff}
.dots i.on{background:var(--accent)}

.services-title{position:absolute;left:144px;top:684px;font-size:17.5px;font-weight:600;color:var(--navy)}
.service-item{position:absolute;left:162px;width:430px;font-size:10px;line-height:15.5px;color:var(--muted)}
.service-item b{font-weight:400;color:var(--navy)}
.service-item svg{position:absolute;left:-16px;top:4px}
.service-plain{position:absolute;left:146px;top:814px;width:460px;font-size:10px;line-height:15.5px;color:var(--muted)}
.map{left:666px;top:683px;width:407px;height:175px;border:4px solid #f2f2f2;box-shadow:0 2px 5px rgba(0,0,0,.25);background:linear-gradient(135deg,#ece8df,#e0dcd2 70%,#c3d6ea)}

.links a{position:absolute;font-size:11.5px;color:#444;text-decoration:none}

.footer{left:0;top:1001px;width:1200px;height:50px;background:linear-gradient(#153f76,#0d3264)}
.footer-name{position:absolute;left:148px;top:15px;font-size:14px;color:#6f8fb8;letter-spacing:1px}
.footer-copy{position:absolute;left:0;width:1280px;top:18px;text-align:center;font-size:11.5px;color:#fff}
</style>
</head>
<body>

<div class="abs top-bar">
  <a style="left:295px">E-Banking</a>
  <a style="left:368px">Masuk</a>
  <a style="left:426px">Tanya Jawab</a>
  <a style="left:517px">Karir &#8250;</a>
  <div class="abs search">Cari
    <svg width="12" height="12" viewBox="0 0 12 12"><circle cx="5" cy="5" r="3.8" fill="none" stroke="#fff" stroke-width="1.6"/><line x1="8" y1="8" x2="11" y2="11" stroke="#fff" stroke-width="1.8"/></svg>
  </div>
  <a style="left:851px">Choose Your Language</a>
  <div class="abs flag"><i style="background:#e2231a"></i><i style="background:#fff"></i></div>
  <svg class="abs" style="left:1043px;top:15px" width="9" height="6"><path d="M0 0h9L4.5 5z" fill="#fff"/></svg>
</div>

<div class="abs header">
  <div class="abs brand"><div class="brand-mark"></div><span class="brand-name">TORVEL CAPITAL</span></div>
  <nav class="nav">
    <a class="active" style="left:491px">Home</a>
    <a style="left:563px">About</a>
    <a style="left:635px">Services</a>
    <a style="left:721px">Current Engagements</a>
    <a style="left:901px">Completed Transactions</a>
  </nav>
</div>

<section class="abs hero">
  <h1 class="hero-title"><b>Trusted or</b> Disciplined<br>Effective?</h1>
  <p class="hero-lead">Torvel Capital is an independent investment bank working for buyers in a number of industries. We</p>
  <div class="btn">Learn More &#8250;</div>
  <div class="abs globe" role="img" aria-label="Globe made of banknote bundles on a brass stand"></div>
  <div class="abs caption">
    <h2 class="caption-title">Sit quet amet solor lsasd <span>Effective?</span></h2>
    <p class="caption-text">Lorem ipsum dolor sit amet, consectetur adipisicing elit, sed do eiusmod tempor incididunt ut <a>labore et dolore magna</a></p>
  </div>
  <div class="abs dots"><i></i><i class="on"></i><i></i><i></i><i></i></div>
</section>

<section>
  <h2 class="services-title">Global Investment Banking Services</h2>
  <div class="service-item" style="top:726px">
    <svg width="11" height="8"><path d="M0 4h9M6 1l3 3-3 3" stroke="#1a4f8f" fill="none" stroke-width="1.3"/></svg>
    <b>Lorem ipsum dolor sit amet</b> - Consectetur adipiscing elit. Sed sagittis consectetur nunc in blandit. Donec aliquam, lacus vel semper congue, sem tellus tincidunt turpisns.
  </div>
  <div class="service-item" style="top:768px">
    <svg width="11" height="8"><path d="M0 4h9M6 1l3 3-3 3" stroke="#1a4f8f" fill="none" stroke-width="1.3"/></svg>
    <b>Lorem ipsum dolor sit amet</b> - Consectetur adipiscing elit. Sed sagittis consectetur nunc in blandit. Donec aliquam, lacus vel semper congue, sem tellusenim.
  </div>
  <p class="service-plain">Lorem ipsum dolor sit amet, consectetur adipiscing elit. Sed sagittis consectetur nunc in blandit. Donec aliquam, lacus vel semper congue, sem tellus tincidunt turpis, a vehicula leo tellus quis</p>
  <div class="abs map" role="img" aria-label="Street map of the office neighbourhood with location pins"></div>
</section>

<div class="links">
  <a style="left:143px;top:901px">VIP Enhanced Online Security</a>
  <a style="left:143px;top:926px">Sitemap</a>
  <a style="left:143px;top:951px">Lost or stolen cards</a>
  <a style="left:400px;top:901px">Disclosure documents</a>
  <a style="left:400px;top:926px">Dispute resolution</a>
  <a style="left:400px;top:951px">Find a branch</a>
  <a style="left:639px;top:901px">VIP Enhanced Online Security</a>
  <a style="left:639px;top:926px">Sitemap</a>
  <a style="left:639px;top:951px">Lost or stolen cards</a>
  <svg class="abs" style="left:882px;top:904px" width="14" height="14"><path d="M12 12L3 3M3 3h6M3 3v6" stroke="#8a1d2c" stroke-width="2.2" fill="none"/></svg>
  <svg class="abs" style="left:885px;top:928px" width="9" height="15"><rect x="0.5" y="0.5" width="8" height="14" rx="1.5" fill="none" stroke="#8a1d2c"/><rect x="2" y="3" width="5" height="6" fill="#8a1d2c"/></svg>
  <svg class="abs" style="left:882px;top:953px" width="14" height="14"><circle cx="7" cy="4" r="3.5" fill="#8a1d2c"/><path d="M0 14a7 6 0 0 1 14 0z" fill="#8a1d2c"/></svg>
  <a style="left:916px;top:901px">VIP Enhanced Online Security</a>
  <a style="left:916px;top:926px">Sitemap</a>
  <a style="left:916px;top:951px">Lost or stolen cards</a>
</div>

<footer class="abs footer">
  <span class="footer-name">TORVEL CAPITAL</span>
  <p class="footer-copy">Copyright Torvel ABN 41 206 538 719 AFSL/japan Credit Licence 518340</p>
</footer>

</body>
</html>
```